Business Card Design

New business card design

Target Market(s)

Residential & Commercial Property Managers

Industry/Entity Type

Plumbing Services

Contact Information for Business Card

Name - Rowan Keddle, title - Director, Phone Number - 0431 286 517, email - rowan@tbk-plumbing.com.au, Company ABN - 73 215 904 386,

Font styles to use
Sans Serif

Colors
0054AA
0677BA
7BADD7
CADEEF
E8F1F8

```html
<!DOCTYPE html>
<html lang="en">
<head>
<meta charset="utf-8">
<title>TBK Plumbing Services – Business Card</title>
<link rel="stylesheet" href="https://fonts.googleapis.com/css2?family=Montserrat:wght@400;500;600&display=swap">
<style>
  :root {
    --backdrop: #2b2c2e;
    --card: #1d232b;
    --card-edge: #29a3dc;
    --accent: #2ea6de;
    --accent-deep: #0677ba;
    --ink-light: #ffffff;
    --ink-muted: #4a4f57;
    --strip: #ffffff;
    --abn-ink: #1d232b;
  }
  * { box-sizing: border-box; margin: 0; padding: 0; }
  html, body {
    width: 1200px; height: 900px; overflow: hidden;
    background: var(--backdrop);
    font-family: "Montserrat", sans-serif;
  }
  .canvas {
    position: relative; width: 1200px; height: 900px;
    display: flex; flex-direction: column; align-items: center; justify-content: center; gap: 46px;
  }
  .card {
    position: relative; width: 630px; height: 360px;
    background: var(--card);
    border-radius: 18px;
    border-bottom: 6px solid var(--card-edge);
    overflow: hidden;
    box-shadow: 0 14px 30px rgba(0,0,0,.45);
  }
  /* Wordmark */
  .wordmark { display: flex; flex-direction: column; align-items: flex-start; }
  .wordmark__name {
    display: flex; align-items: center; gap: 14px;
    font-weight: 500; color: var(--ink-light); letter-spacing: 2px; line-height: 1;
  }
  .wordmark__dot { border-radius: 50%; background: var(--accent); flex: none; }
  .wordmark__tagline {
    color: var(--ink-muted); text-transform: lowercase; letter-spacing: 9px; font-size: 13px;
  }
  /* Front */
  .card--front { display: flex; align-items: center; justify-content: center; }
  .card--front .wordmark__name { font-size: 96px; }
  .card--front .wordmark__dot { width: 22px; height: 22px; }
  .card--front .wordmark__tagline { margin-top: 14px; margin-left: 6px; }
  /* Back */
  .card--back .wordmark { position: absolute; left: 40px; top: 34px; }
  .card--back .wordmark__name { font-size: 76px; }
  .card--back .wordmark__dot { width: 18px; height: 18px; }
  .card--back .wordmark__tagline { margin-top: 10px; font-size: 11px; letter-spacing: 8px; }
  .person { position: absolute; left: 56px; top: 170px; }
  .person__name { color: var(--accent); font-weight: 600; font-size: 24px; }
  .person__role { color: var(--ink-light); font-size: 15px; margin-top: 2px; }
  .contacts { position: absolute; left: 56px; top: 236px; list-style: none; }
  .contacts li {
    display: flex; align-items: center; gap: 12px;
    color: var(--ink-light); font-size: 14px; height: 24px;
  }
  .contacts svg { width: 14px; height: 14px; fill: var(--accent); flex: none; }
  .band {
    position: absolute; left: 0; bottom: 0; width: 330px; height: 36px; background: var(--accent);
  }
  .abn-strip {
    position: absolute; right: 0; bottom: 0; width: 290px; height: 36px; background: var(--strip);
    display: flex; align-items: center; justify-content: center;
    font-size: 14px; color: var(--abn-ink);
  }
  .abn-strip strong { color: var(--accent-deep); font-weight: 600; margin-right: 6px; }
</style>
</head>
<body>
<main class="canvas">
  <section class="card card--front" aria-label="Card front">
    <div class="wordmark">
      <div class="wordmark__name"><span>tbk</span><span class="wordmark__dot"></span></div>
      <div class="wordmark__tagline">plumbing services</div>
    </div>
  </section>

  <section class="card card--back" aria-label="Card back">
    <div class="wordmark">
      <div class="wordmark__name"><span>tbk</span><span class="wordmark__dot"></span></div>
      <div class="wordmark__tagline">plumbing services</div>
    </div>
    <div class="person">
      <p class="person__name">Rowan Keddle</p>
      <p class="person__role">Director</p>
    </div>
    <ul class="contacts">
      <li><svg viewBox="0 0 24 24" aria-hidden="true"><path d="M6.6 10.8a15 15 0 0 0 6.6 6.6l2.2-2.2c.3-.3.7-.4 1-.2 1.1.4 2.3.6 3.6.6.6 0 1 .4 1 1V20c0 .6-.4 1-1 1A17 17 0 0 1 3 4c0-.6.4-1 1-1h3.5c.6 0 1 .4 1 1 0 1.3.2 2.5.6 3.6.1.3 0 .7-.2 1z"/></svg>0431 286 517</li>
      <li><svg viewBox="0 0 24 24" aria-hidden="true"><path d="M2 5h20v14H2z M2 5l10 8 10-8" /></svg>rowan@tbk-plumbing.com.au</li>
      <li><svg viewBox="0 0 24 24" aria-hidden="true"><circle cx="12" cy="12" r="10"/></svg>www.tbk-plumbing.com.au</li>
    </ul>
    <div class="band"></div>
    <div class="abn-strip"><strong>ABN</strong> - 73 215 904 386</div>
  </section>
</main>
</body>
</html>
```